Modern Business Card

Modern professional business card with more than just logo and demographic info. Something memorable.

We are a trendy/modern chiropractic group with an emphasis on neurology, hence the minimalist-type brain logo. We want to convey that modern and technical aspect with professionalism and the elite nature of our practice environment.

```html
<!DOCTYPE html>
<html lang="en">
<head>
<meta charset="UTF-8">
<title>Cadence Chiropractic – Business Card</title>
<link href="https://fonts.googleapis.com/css2?family=Open+Sans:wght@400;600;700&display=swap" rel="stylesheet">
<style>
  :root {
    --brand-blue: #5a8fcb;
    --ink: #1c1c1c;
    --ink-soft: #3a3a3a;
    --paper: #ffffff;
    --backdrop: #e9e7e3;
  }
  * { margin: 0; padding: 0; box-sizing: border-box; }
  html, body {
    width: 1200px; height: 780px; overflow: hidden;
    background: var(--backdrop);
    font-family: "Open Sans", Arial, sans-serif;
    color: var(--ink);
  }
  .canvas {
    width: 1200px; height: 780px;
    display: flex; align-items: center; justify-content: center; gap: 44px;
  }
  .card {
    position: relative;
    width: 540px; height: 308px;
    background: var(--paper);
    border-radius: 10px;
    overflow: hidden;
    box-shadow: 0 6px 18px rgba(0,0,0,0.12);
  }

  /* Front side */
  .front .corner-tab {
    position: absolute; left: 40px; top: 0;
    width: 54px; height: 7px; background: var(--brand-blue);
  }
  .front .bottom-band {
    position: absolute; left: 0; right: 0; bottom: 0;
    height: 14px; background: var(--brand-blue);
  }
  .front .identity { position: absolute; left: 40px; top: 30px; }
  .front .person-name {
    font-size: 25px; letter-spacing: 0.5px; line-height: 1.1;
    text-transform: uppercase;
  }
  .front .person-name strong { font-weight: 700; }
  .front .person-name span { font-weight: 400; }
  .front .person-role {
    font-size: 13px; letter-spacing: 0.6px; color: var(--ink-soft);
    text-transform: uppercase; margin-top: 2px;
  }
  .front .divider {
    position: absolute; left: 40px; top: 104px; width: 402px; height: 1px;
    background: var(--ink);
  }
  .front .divider::before {
    content: ""; position: absolute; left: 0; top: -1px;
    width: 132px; height: 3px; background: var(--brand-blue);
  }
  .front .brand {
    position: absolute; right: 34px; top: 118px;
    display: flex; align-items: center; gap: 9px;
  }
  .brand-square { width: 16px; height: 16px; background: var(--brand-blue); flex: none; }
  .front .brand-name {
    font-size: 15px; font-weight: 600; letter-spacing: 1.2px;
    color: var(--ink); text-transform: uppercase; line-height: 1.2;
  }
  .contact-list {
    position: absolute; left: 40px; top: 130px;
    list-style: none; display: flex; flex-direction: column; gap: 14px;
  }
  .contact-item { display: flex; align-items: center; gap: 12px; font-size: 14px; }
  .icon-box {
    width: 22px; height: 22px; border-radius: 2px; background: var(--brand-blue);
    display: flex; align-items: center; justify-content: center; flex: none;
  }
  .address {
    position: absolute; right: 34px; bottom: 40px;
    display: flex; align-items: flex-start; gap: 12px;
  }
  .address-text { font-size: 14px; line-height: 1.35; }

  /* Back side */
  .back .brand-band {
    position: absolute; left: 0; right: 0; top: 54px; height: 138px;
    background: var(--brand-blue);
    display: flex; align-items: center; justify-content: center; gap: 14px;
  }
  .back .brand-square { width: 26px; height: 26px; background: var(--paper); }
  .back .brand-name {
    color: var(--paper); font-size: 26px; font-weight: 600;
    letter-spacing: 2px; text-transform: uppercase; line-height: 1.15;
  }
  .back .web-row {
    position: absolute; left: 0; right: 0; top: 236px;
    display: flex; align-items: center; gap: 16px; padding: 0 0;
  }
  .back .rule { flex: 1; height: 1px; background: var(--brand-blue); }
  .back .web-address { font-size: 14px; color: var(--brand-blue); letter-spacing: 0.4px; }
</style>
</head>
<body>
<main class="canvas">

  <section class="card front" aria-label="Card front">
    <div class="corner-tab"></div>

    <div class="identity">
      <h1 class="person-name"><strong>Jordan</strong> <span>Hale</span></h1>
      <p class="person-role">Founder &amp; CEO</p>
    </div>

    <div class="divider"></div>

    <div class="brand">
      <div class="brand-square"></div>
      <div class="brand-name">Cadence<br>Chiropractic</div>
    </div>

    <ul class="contact-list">
      <li class="contact-item">
        <span class="icon-box">
          <svg width="12" height="12" viewBox="0 0 12 12"><rect x="3" y="1" width="6" height="10" rx="1" fill="none" stroke="#fff" stroke-width="1.3"/><circle cx="6" cy="9" r="0.7" fill="#fff"/></svg>
        </span>
        012-555-0147
      </li>
      <li class="contact-item">
        <span class="icon-box">
          <svg width="12" height="12" viewBox="0 0 12 12"><circle cx="3" cy="9" r="1.2" fill="#fff"/><path d="M3 6a3 3 0 0 1 3 3M3 3a6 6 0 0 1 6 6" fill="none" stroke="#fff" stroke-width="1.3"/></svg>
        </span>
        www.cadencechiro.com
      </li>
    </ul>

    <div class="address">
      <div class="address-text">Address, Suit, Floor<br>City, Country, Zipcode</div>
      <span class="icon-box">
        <svg width="12" height="12" viewBox="0 0 12 12"><path d="M6 11C3.5 8 2.5 6.3 2.5 4.7a3.5 3.5 0 0 1 7 0C9.5 6.3 8.5 8 6 11z" fill="#fff"/><circle cx="6" cy="4.7" r="1.3" fill="#5a8fcb"/></svg>
      </span>
    </div>

    <div class="bottom-band"></div>
  </section>

  <section class="card back" aria-label="Card back">
    <div class="brand-band">
      <div class="brand-square"></div>
      <div class="brand-name">Cadence<br>Chiropractic</div>
    </div>
    <div class="web-row">
      <span class="rule"></span>
      <span class="web-address">www.cadencechiro.com</span>
      <span class="rule"></span>
    </div>
  </section>

</main>
</body>
</html>
```